Large online photo magazine needs redesign

We have previously digitised a historical photographic magazine of around 20,000 printed pages and made it available online. The magazine ran up to the early 1970s, and the content is largely black and white photographs of local events, accompanied by short captions.

Although the content is very rich, the design needs to be revisited so that:
* it is visually appealing
* it is responsive (i.e. works in browsers across all manner of devices)
* is faithful to the nature of the content

There are only a few core page types, and the central one is the article page, an example of which can be seen at:
http://snapgazette.example/gisborne/issue/KLR48_19600714/t1-body-d4.html

Any design submitted should be based on the treatment of an article page such as the above.

Given the large number of pages on our site, we need a design which can be templated to work for any content in the collection, i.e. we cannot hand-craft our templates to match a given page of content, rather a template must work acceptably well for all content.

The current site, although basic in design, has the advantage that it is quite efficient in the amount of data per page request (around 100k - 200k). While not adverse to web fonts, banner imagery etc, we will carefully consider the benefit gained from any such treatment against the amount of extra data that needs to be downloaded to the client's browser.

For the right design, we are able ourselves to adapt it to a CSS layout.

An example of each core page type is as follows (though for this project we only expect a design for a single page, as itemised above):

http://snapgazette.example/gisborne/index.html
http://snapgazette.example/gisborne/about.html
http://snapgazette.example/gisborne/help.html
http://snapgazette.example/gisborne/initial/index.html
http://snapgazette.example/gisborne/search/results?type=section&text=smith&cmdSubmit=Go
http://snapgazette.example/gisborne/advanced-search/index.html
http://snapgazette.example/gisborne/issue/KLR48_19600714/t1-front-d1.html
http://snapgazette.example/gisborne/issue/KLR48_19600714/index.html
http://snapgazette.example/gisborne/issue/KLR48_19600714/fig-KLR48_19600714_005a.html
http://snapgazette.example/gisborne/issue/KLR48_19600714/KLR48_19600714_012.html
http://snapgazette.example/gisborne/issue/KLR48_19600714/thumbnails.html

Target Market(s)

A general browsing audience of all ages, but skewed towards the older generations, and those interested in family / regional history.

The average user will not be particularly web-savy, and the treatment of the content should not detract / distract from the actual content itself.

Industry/Entity Type

Events

Requirements
Must have
• * it is visually appealing
The content should be visually appealing to the audience, which can be defined as a general browsing audience of all ages, but skewed towards the middle and older generations.

* it is responsive (the design can be adapted - by us - to work in browsers across all manner of devices)

The magazine covers (http://snapgazette.example/gisborne/issues/index.html) offer some possible inspiration for treatment of the material.

```html
<!DOCTYPE html>
<html lang="en">
<head>
<meta charset="utf-8">
<title>Flying Sisters from Gisborne – Gisborne Snap Gazette</title>
<link rel="stylesheet" href="https://fonts.googleapis.com/css2?family=Open+Sans:wght@400;600;700&display=swap">
<style>
:root{
  --brand:#cb3a51;
  --brand-dark:#4a1322;
  --brand-darker:#3a0d19;
  --nav-active:#f58aa6;
  --cream:#f6efe0;
  --ink:#333;
  --muted:#666;
  --link:#6b1a2c;
  --crumb-link:#c23a50;
  --bar-dark:#555;
  --bar-light:#e8e0cc;
  --rule:#ddd;
  --footer:#e8e8e8;
  --frame:#dcdcdc;
  --sepia-a:#d9ccaa;
  --sepia-b:#9b9178;
}
*{box-sizing:border-box;margin:0;padding:0}
html,body{width:1200px;height:975px;overflow:hidden}
body{font-family:"Open Sans",Arial,sans-serif;color:var(--ink);background:#fff;position:relative}
a{color:inherit;text-decoration:none}
.wrap{width:1001px;margin:0 auto;position:relative}

.masthead{height:81px;background:var(--brand);display:flex;align-items:center;justify-content:center;gap:12px}
.masthead .mark{width:26px;height:26px;background:var(--cream)}
.masthead .name{font-size:36px;font-weight:700;color:var(--cream);letter-spacing:1px}

.mainnav{height:50px;background:linear-gradient(var(--brand-dark),var(--brand-darker))}
.mainnav .wrap{display:flex;align-items:center;height:50px}
.mainnav ul{list-style:none;display:flex;gap:0}
.mainnav li a{display:block;color:#fff;font-size:14.5px;padding:0 22px;line-height:50px;text-transform:uppercase}
.mainnav li:first-child a{padding-left:27px;color:var(--nav-active)}
.search{margin-left:auto;width:268px;height:34px;background:var(--cream);border-radius:3px;display:flex;align-items:center;padding:0 10px;font-size:12px;color:#888}
.search svg{margin-left:auto}

.crumbs{display:flex;font-size:12.5px;margin-top:20px;height:20px;align-items:center;color:var(--muted)}
.crumbs a:first-child{color:var(--crumb-link)}
.crumbs .sep{margin:0 8px;color:#aaa}
.crumbs .report{margin-left:auto;color:var(--ink)}

.issuebar{margin-top:16px;height:37px;border-radius:3px;background:linear-gradient(90deg,#efe9dc,var(--bar-light));display:flex;align-items:center;font-size:14px}
.issuebar .date{background:var(--bar-dark);color:#fff;font-weight:600;height:37px;line-height:37px;padding:0 18px;border-radius:3px 0 0 3px;position:relative}
.issuebar .date:after{content:"";position:absolute;right:-14px;top:0;border-left:14px solid var(--bar-dark);border-top:18.5px solid transparent;border-bottom:18.5px solid transparent}
.issuebar .page{background:#d6ccb6;height:37px;line-height:37px;padding:0 16px 0 26px;font-size:18px;color:#555}
.pager{margin-left:auto;display:flex;align-items:center;gap:10px;padding-right:12px;font-size:14px;color:var(--ink)}
.pager .prev{color:var(--link)}
.pager .slash{color:#aaa}

h1{font-weight:400;font-size:23px;color:var(--brand);margin-top:29px}

.article{display:flex;margin-top:18px;gap:20px}
.gallery{width:489px;margin-left:4px}
.plate{display:block;border:4px solid var(--frame);width:489px;height:323px;background:linear-gradient(135deg,var(--sepia-a),var(--sepia-b))}
.thumbs{display:flex;gap:7px;margin-top:9px}
.thumb{border:4px solid var(--frame);width:159px;height:116px;background:linear-gradient(135deg,#bdbdbd,#4e4e4e)}
.thumb.bridge{background:linear-gradient(#cfcfcf,#7a7a7a)}
.body{flex:1;font-size:13.5px;line-height:23px;color:var(--muted)}
.share{display:flex;gap:10px;margin-top:16px;font-size:11px}
.share .btn{display:flex;align-items:center;gap:4px;height:20px;padding:0 5px;border:1px solid #c9c9c9;border-radius:3px;background:#f2f2f2;color:#333}
.share .btn i{width:11px;height:11px;background:#999;display:block}
.share .btn.hot{background:#e8604c;border-color:#e8604c;color:#fff}
.share .btn.hot i{background:#fff}
.share .count{height:20px;line-height:18px;padding:0 5px;border:1px solid #ccc;border-radius:2px;background:#fff;color:#333}
.share .group{display:flex;gap:4px}

.endnav{border-top:1px solid var(--rule);margin-top:39px;padding-top:16px;display:flex}

.footer{position:absolute;left:0;right:0;top:862px;bottom:0;background:var(--footer)}
.footer .wrap{padding-top:27px;font-size:13px;color:var(--ink)}
.footer nav{display:flex;gap:12px}
.footer nav .sep{color:#aaa}
.copy{margin-top:15px}
.footer .badges{position:absolute;right:0;top:40px;display:flex;gap:8px;align-items:center}
.footer .sq{width:24px;height:24px;background:#3b5b98;border-radius:3px}
.footer .sq.alt{background:#4fb3e6}
.footer .licence{width:92px;height:32px;background:#222;border:2px solid #999;margin-left:12px}
</style>
</head>
<body>
<header class="masthead">
  <span class="mark"></span><span class="name">Gisborne Snap Gazette</span>
</header>
<nav class="mainnav">
  <div class="wrap">
    <ul>
      <li><a href="http://snapgazette.example/gisborne/index.html">Home</a></li>
      <li><a href="http://snapgazette.example/gisborne/about.html">About</a></li>
      <li><a href="http://snapgazette.example/gisborne/issues/index.html">Browse Gisborne Snap Gazette</a></li>
      <li><a href="http://snapgazette.example/gisborne/initial/index.html">A-Z People</a></li>
      <li><a href="http://snapgazette.example/gisborne/help.html">Help</a></li>
    </ul>
    <div class="search">Search Gisborne Snap Gazette
      <svg width="22" height="22" viewBox="0 0 22 22"><circle cx="9" cy="9" r="6.5" fill="none" stroke="#888" stroke-width="3"/><line x1="14" y1="14" x2="20" y2="20" stroke="#888" stroke-width="4" stroke-linecap="round"/></svg>
    </div>
  </div>
</nav>
<main class="wrap">
  <div class="crumbs">
    <a href="http://snapgazette.example/gisborne/index.html">Gisborne Snap Gazette</a><span class="sep">»</span>
    <a href="http://snapgazette.example/gisborne/issues/index.html">Issues</a><span class="sep">»</span>
    <a href="http://snapgazette.example/gisborne/issue/KLR48_19600714/index.html">KLR48_19600714</a><span class="sep">»</span>
    <span>t1-body-d4</span>
    <a class="report" href="#">Report an error</a>
  </div>
  <div class="issuebar">
    <span class="date">No 73 July 14, 1960</span><span class="page">5</span>
    <div class="pager">
      <a class="prev" href="#">Previous article</a><span class="slash">/</span>
      <a href="http://snapgazette.example/gisborne/issue/KLR48_19600714/index.html">Issue contents</a><span class="slash">/</span>
      <a href="#">Next article</a><span class="slash">/</span>
      <svg width="20" height="20" viewBox="0 0 20 20"><rect x="5" y="2" width="10" height="6" fill="#444"/><rect x="1" y="8" width="18" height="7" rx="2" fill="#444"/><rect x="5" y="13" width="10" height="6" fill="#444" stroke="#fff"/></svg>
    </div>
  </div>
  <h1>Flying Sisters from Gisborne</h1>
  <section class="article">
    <div class="gallery">
      <div class="plate" role="img" aria-label="Scanned magazine spread with portraits, engagement notices, air hostesses and a bridge"></div>
      <div class="thumbs">
        <div class="thumb" role="img" aria-label="Three air hostesses in uniform"></div>
        <div class="thumb" role="img" aria-label="Air hostess at an aircraft door"></div>
        <div class="thumb bridge" role="img" aria-label="Bridge over a river with caption"></div>
      </div>
    </div>
    <div class="body">
      <p>Donec fringilla odio sit amet ipsum cursus, sed lobortis odio molestie. Donec id ultrices nunc. Maecenas eleifend ullamcorper est nec laoreet. Vestibulum adipiscing vehicula feugiat. Ut tempor euismod nibh, egestas blandit arcu pellentesque quis. Integer in metus rhoncus, fringilla est quis, semper lectus. Proin ornare aliquam laoreet. Phasellus congue velit at massa congue blandit. Vestibulum at eleifend augue, at gravida tortor. Fusce eu lacus felis. Donec et velit nulla. Cras aliquet urna sed tempor fermentum.</p>
      <div class="share">
        <span class="group"><span class="btn"><i></i>Like</span><span class="count">3k</span></span>
        <span class="group"><span class="btn"><i></i>Post</span><span class="count">316</span></span>
        <span class="group"><span class="btn"><i></i>+1</span><span class="count">81</span></span>
        <span class="group"><span class="btn hot"><i></i>Share</span><span class="count">4.6K</span></span>
      </div>
    </div>
  </section>
  <div class="endnav">
    <div class="pager">
      <a class="prev" href="#">Previous article</a><span class="slash">/</span>
      <a href="http://snapgazette.example/gisborne/issue/KLR48_19600714/index.html">Issue contents</a><span class="slash">/</span>
      <a href="#">Next article</a><span class="slash">/</span>
      <svg width="20" height="20" viewBox="0 0 20 20"><rect x="5" y="2" width="10" height="6" fill="#444"/><rect x="1" y="8" width="18" height="7" rx="2" fill="#444"/><rect x="5" y="13" width="10" height="6" fill="#444" stroke="#fff"/></svg>
    </div>
  </div>
</main>
<footer class="footer">
  <div class="wrap">
    <nav>
      <a href="http://snapgazette.example/gisborne/index.html">Home</a><span class="sep">|</span>
      <a href="http://snapgazette.example/gisborne/about.html">About</a><span class="sep">|</span>
      <a href="http://snapgazette.example/gisborne/issues/index.html">Browse Gisborne Snap Gazette</a><span class="sep">|</span>
      <a href="http://snapgazette.example/gisborne/initial/index.html">A-Z people</a><span class="sep">|</span>
      <a href="http://snapgazette.example/gisborne/help.html">Help</a>
    </nav>
    <p class="copy">Copyright &copy; 2014 &nbsp;&nbsp; Snap Gazette. &nbsp;&nbsp;All rights reserved.</p>
    <div class="badges"><span class="sq"></span><span class="sq alt"></span><span class="licence"></span></div>
  </div>
</footer>
</body>
</html>
```